July 2022 Industrial Manufacturer Product Expo Mexico City

We manufacture large screws and fastners for large Mining equipment, Trains, large ships, airplanes, wind turbines, and so on. We also do custom work base on the customer needs. No matter the size we can make it.
We have a Expo coming up with companies all over the world. We have to stand out we are a family own business so our customer service will be above and beyond anyone can provide. We do not have a sales force to push our products and services we provide one on one service.
Plus@!! I'm looking for anything that you designers can come up with if it was your company to put on a business card, plus i want to do a 1 or 2 sided pamphlet, and then a website. We make Speciality Bolts for large mining equipment these bolts can be 3 to 4 foot long!!! Plus fasteners, Nuts, washers, any, size, strengths, special materials, we offer more of a ono on one customer service, We are a small company, family own, but can fulfill any type of orders. We can also provide special time lines for emergency orders. "We keep the machines running we here at KRV don't believe in down time" We want to hear any slogan based on our company to stand out.
Thanks i really appreciate all your work and options that we have to pick on. Plus just a thought we could possibly want to entertain a experience Marketing internet help maybe a employment possibility. Thanks

I need 2 cards one in Spanish and English Like the steel back ground maybe send me in some bright red and blue writing Same with the Black cards Please remove the word Military The logo KRV maybe integrate a picture of a Bolt 🔩 Thank you

Still looking for I need 2 cards one in Spanish and English Like the steel back ground maybe send me in some bright red and blue writing Same with the Black cards try bright writing Please remove the word Military The logo KRV maybe integrate a picture of a Bolt 🔩 Plus will need the company to make a brochure and website next Thank you

Target Market(s)

Large Mining, Ship, Train, Green Energy, VELM, and Government equipment. Throughout the World

Industry/Entity Type

We can Custom Manufacture any type of Fastners for Mining equipment, Trains, Ships, Green energy, Governments, or military projects. wind turbines,

Contact Information for Business Card

I attached the name and contact info that's on a card, plus the Company Logo. Would like industrial looking background with Bright Colors that will stand out!! If we can insert somewhere maybe on back that we "Custom Manufacture Any Size or Quantity Fastners for Large Mining Equipment, Trains, Ships, Green Energy Equipment or Government Projects

Font styles to use
Other font styles liked:
• You Pick, has to be bold, colorful standout, Professional looking Beable to read it.

Colors

Designer to choose colors to be used in the design.

Requirements
Must have
• Need in Spanish and English TO STANDOUT FROM THE REST OF THE EXPO!! See Business card details, Rounded corners
Nice to have
• Can i see some of the darker cards with Bright Red and Blue letters I like to see the different type of card material, heavy thickness, plastic, transparent, Metal types, Bright Colors, I saw like Raised letters like on the logo.

```html
<!DOCTYPE html>
<html lang="en">
<head>
<meta charset="utf-8">
<title>KRV Business Card – Front and Back</title>
<link href="https://fonts.googleapis.com/css2?family=Comfortaa:wght@400;600;700&display=swap" rel="stylesheet">
<style>
  :root {
    --page-bg: #ece9e5;
    --card-frost: #c8c8ca;
    --card-frost-edge: #b4b4b7;
    --band-white: #ffffff;
    --text-grey: #4a4a4d;
    --icon-blue: #1ba1e2;
    --brand-blue: #1f5fae;
  }
  html, body {
    margin: 0;
    padding: 0;
    width: 1200px;
    height: 800px;
    overflow: hidden;
    background: var(--page-bg);
    font-family: "Comfortaa", sans-serif;
  }
  .canvas {
    position: relative;
    width: 1200px;
    height: 800px;
  }
  .card {
    position: absolute;
    top: 245px;
    width: 520px;
    height: 310px;
    border-radius: 22px;
    background: var(--card-frost);
    border: 1px solid var(--card-frost-edge);
    box-shadow: 0 14px 30px rgba(0,0,0,0.18);
    overflow: hidden;
  }
  .card--front { left: 50px; }
  .card--back { left: 630px; }

  .brand-name {
    position: absolute;
    font-family: "Comfortaa", sans-serif;
    font-weight: 700;
    font-size: 58px;
    letter-spacing: 6px;
    color: var(--brand-blue);
    line-height: 1;
  }
  .card--front .brand-name { top: 38px; right: 60px; }
  .card--back .brand-name { top: 30px; right: 40px; }

  .white-band {
    position: absolute;
    left: 0;
    right: 0;
    background: var(--band-white);
  }
  .card--front .white-band { top: 130px; height: 150px; }
  .card--back .white-band { top: 110px; height: 150px; }

  .contact-block {
    padding: 14px 28px;
    color: var(--text-grey);
  }
  .contact-name {
    margin: 0;
    font-size: 19px;
    font-weight: 600;
    letter-spacing: 0.5px;
  }
  .contact-note {
    margin: 2px 0 14px;
    font-size: 17px;
    font-weight: 600;
  }
  .contact-list {
    list-style: none;
    margin: 0;
    padding: 0;
    font-size: 15px;
  }
  .contact-list li {
    display: flex;
    align-items: center;
    gap: 10px;
    margin-bottom: 6px;
  }
  .contact-icon {
    width: 16px;
    height: 16px;
    flex: none;
  }

  .tagline {
    margin: 0;
    height: 100%;
    display: flex;
    flex-direction: column;
    justify-content: center;
    align-items: center;
    text-align: center;
    color: var(--text-grey);
    font-size: 16px;
    font-weight: 600;
    line-height: 1.65;
    letter-spacing: 0.4px;
  }
</style>
</head>
<body>
<main class="canvas">

  <section class="card card--front" aria-label="Business card front">
    <div class="brand-name">KRV</div>
    <div class="white-band">
      <div class="contact-block">
        <p class="contact-name">Lic. Marisol Ortega Vidal</p>
        <p class="contact-note">quotes in</p>
        <ul class="contact-list">
          <li>
            <svg class="contact-icon" viewBox="0 0 16 16" aria-hidden="true">
              <path fill="var(--icon-blue)" d="M2 6c0-2 2-3 6-3s6 1 6 3v1h-3V5.5H5V7H2zM4 8h8l1 6H3z"/>
            </svg>
            <span>555 0148230</span>
          </li>
          <li>
            <svg class="contact-icon" viewBox="0 0 16 16" aria-hidden="true">
              <rect x="4" y="1" width="8" height="14" rx="1.5" fill="none" stroke="var(--icon-blue)" stroke-width="1.6"/>
              <circle cx="8" cy="12.5" r="0.9" fill="var(--icon-blue)"/>
            </svg>
            <span>5550193746</span>
          </li>
          <li>
            <svg class="contact-icon" viewBox="0 0 16 16" aria-hidden="true">
              <rect x="1" y="4" width="14" height="10" rx="1" fill="var(--icon-blue)"/>
              <path d="M1.5 4.5 8 9.5l6.5-5" fill="none" stroke="#ffffff" stroke-width="1.2"/>
            </svg>
            <span>pernosvidal.ventas@example.com</span>
          </li>
        </ul>
      </div>
    </div>
  </section>

  <section class="card card--back" aria-label="Business card back">
    <div class="brand-name">KRV</div>
    <div class="white-band">
      <p class="tagline">
        <span>Custom Manufacture Any Size or</span>
        <span>Quantity Fastners for Large Mining Equipment</span>
        <span>Trains, Ships, Green Energy Equipment</span>
        <span>or Government Projects</span>
      </p>
    </div>
  </section>

</main>
</body>
</html>
```